HVAC Company Business Card design with attached logo

Looking for an easily readable and attractive business card design that includes my attached company logo. I selected one sided card because it's more traditional, but I'm open to a 2-sided design. All of the details should be included in the design. Looking to create a professional, upscale image.

Target Market(s)

Commercial and residential consumers

Industry/Entity Type

Hvac

Contact Information for Business Card

Company phone number is 631.487.2953
Company email marcus@tidewellhvac.example
Company name is Bright Harbor Air Conditioning, Refrigeration, and Heating
Marcus Delgado
Owner Operator
Company Address is
PO Box 872,
712 Fenwyck Ln,
Alder Point, NJ 11752
Business License K8195240000
Insured

Font styles to use
Serif
Sans Serif

Colors

Designer to choose colors to be used in the design.

Requirements
Must have
• Must include the logo.
Nice to have
• It seems like it should be a one sided card, but I'm open to a 2 sided one.

```html
<!DOCTYPE html>
<html lang="en">
<head>
<meta charset="UTF-8">
<title>Bright Harbor – Business Card</title>
<link rel="stylesheet" href="https://fonts.googleapis.com/css2?family=Oswald:wght@500&family=Work+Sans:wght@400;500;600&display=swap">
<style>
  :root {
    --page-bg: #1c1c1e;
    --card-bg: #2b2b2d;
    --text-light: #f2f2f2;
    --text-muted: #d9d9d9;
    --accent: #e8672a;
    --logo-silver: #b9b9bb;
  }
  * { box-sizing: border-box; margin: 0; padding: 0; }
  html, body {
    width: 1200px; height: 1000px; overflow: hidden;
    background: var(--page-bg);
    font-family: "Work Sans", Arial, sans-serif;
  }
  .sheet {
    width: 1200px; height: 1000px;
    display: flex; flex-direction: column; align-items: center; justify-content: center;
    gap: 60px;
  }
  .card {
    position: relative;
    width: 700px; height: 400px;
    background: var(--card-bg);
    box-shadow: 0 14px 30px rgba(0,0,0,.55);
  }
  /* Front */
  .card-front { display: flex; align-items: center; justify-content: center; }
  .brand { display: flex; align-items: center; gap: 18px; }
  .brand-mark {
    width: 58px; height: 58px; border-radius: 50%;
    background: var(--logo-silver);
  }
  .brand-name {
    font-family: "Work Sans", Arial, sans-serif;
    font-weight: 600; font-size: 50px; letter-spacing: 1px;
    color: var(--logo-silver); text-transform: uppercase;
  }
  /* Back */
  .license {
    position: absolute; top: 48px; right: 40px;
    font-size: 15px; letter-spacing: 1.5px; color: var(--text-muted);
  }
  .identity {
    position: absolute; top: 148px; left: 60px; right: 24px;
    display: flex; align-items: center;
  }
  .person { text-align: right; padding-right: 22px; flex: none; }
  .person-name {
    font-family: "Oswald", "Arial Narrow", sans-serif;
    font-weight: 500; font-size: 38px; color: var(--text-light);
    text-transform: uppercase; line-height: 1.1;
  }
  .person-title {
    font-size: 18px; font-weight: 500; letter-spacing: 1.5px;
    color: var(--accent); margin-top: 4px;
  }
  .divider { width: 2px; height: 80px; background: var(--text-light); flex: none; }
  .contact-list { list-style: none; padding-left: 20px; }
  .contact-list li {
    display: flex; align-items: center; gap: 14px;
    font-size: 16px; letter-spacing: 1px; color: var(--text-muted);
    line-height: 26px; white-space: nowrap;
  }
  .contact-list svg, .address svg { flex: none; fill: var(--accent); }
  .address {
    position: absolute; left: 40px; bottom: 52px;
    display: flex; align-items: center; gap: 12px;
    font-size: 17px; letter-spacing: 1.2px; color: var(--text-muted);
  }
</style>
</head>
<body>
<main class="sheet">
  <section class="card card-front" aria-label="Card front">
    <div class="brand">
      <span class="brand-mark"></span>
      <span class="brand-name">Bright Harbor</span>
    </div>
  </section>

  <section class="card card-back" aria-label="Card back">
    <p class="license">License K8195240000</p>

    <div class="identity">
      <div class="person">
        <h1 class="person-name">Marcus Delgado</h1>
        <p class="person-title">Owner Operator</p>
      </div>
      <span class="divider"></span>
      <ul class="contact-list">
        <li>
          <svg width="16" height="16" viewBox="0 0 24 24" aria-hidden="true"><path d="M6.6 10.8a15.1 15.1 0 0 0 6.6 6.6l2.2-2.2c.3-.3.7-.4 1-.2 1.1.4 2.3.6 3.6.6.6 0 1 .4 1 1V20c0 .6-.4 1-1 1A17 17 0 0 1 3 4c0-.6.4-1 1-1h3.5c.6 0 1 .4 1 1 0 1.3.2 2.5.6 3.6.1.3 0 .7-.2 1z"/></svg>
          631.487.2953
        </li>
        <li>
          <svg width="16" height="16" viewBox="0 0 24 24" aria-hidden="true"><path d="M2 5h20v2l-10 6L2 7zM2 9l10 6 10-6v10H2z"/></svg>
          marcus@tidewellhvac.example
        </li>
        <li>
          <svg width="16" height="16" viewBox="0 0 24 24" aria-hidden="true"><path d="M12 2a10 10 0 1 0 0 20 10 10 0 0 0 0-20zm6.9 6h-2.9a15.7 15.7 0 0 0-1.4-3.6A8 8 0 0 1 18.9 8zM12 4a14 14 0 0 1 1.9 4h-3.8A14 14 0 0 1 12 4zM4.3 14a8 8 0 0 1 0-4h3.4a16.5 16.5 0 0 0 0 4zm.8 2h2.9c.3 1.3.8 2.5 1.4 3.6A8 8 0 0 1 5.1 16zM8 8H5.1a8 8 0 0 1 4.3-3.6C8.8 5.5 8.3 6.7 8 8zm4 12a14 14 0 0 1-1.9-4h3.8A14 14 0 0 1 12 20zm2.3-6H9.7a14.7 14.7 0 0 1 0-4h4.6a14.7 14.7 0 0 1 0 4zm.3 5.6c.6-1.1 1.1-2.3 1.4-3.6h2.9a8 8 0 0 1-4.3 3.6zm1.7-5.6a16.5 16.5 0 0 0 0-4h3.4a8 8 0 0 1 0 4z"/></svg>
          www.tidewellhvac.example
        </li>
      </ul>
    </div>

    <p class="address">
      <svg width="16" height="22" viewBox="0 0 16 22" aria-hidden="true"><path d="M8 0a8 8 0 0 0-8 8c0 6 8 14 8 14s8-8 8-14a8 8 0 0 0-8-8zm0 11a3 3 0 1 1 0-6 3 3 0 0 1 0 6z"/></svg>
      PO Box 872, 712 Fenwyck Ln, Alder Point, NJ 11752
    </p>
  </section>
</main>
</body>
</html>
```